UI/UX Re-Do for TallyNest - a free to use project management platform for desktop and mobile.

UI/UX Re-Do for TallyNest
TallyNest is a free to use project management platform for desktop and mobile.
We are looking for help with our UI/UX re-design.
As of now the platform is totally functional.
The problem is around flow and look. We want TN to become something that any one can use to manage and even socialize any project. A project can be something work related like organizing a team around a software build, marketing campaign, shared client file space, etc... In fact, most of our current members are using TN for just such work projects.
We also see a project as planning a wedding, organizing a group trip, a simple to-do list, organizing a kids sports team, and so on...
To become a platform that people will use in their work and personal life we first need to become more intuitive and friendly - while maintaining advanced functionality for more advanced needs.
We need help to beautify, streamline, and simplify - while keeping all the functions.
The quickest way to understand TN, and our current issues is this short video:
https://vidlumo.example/w/Qa7KdP2mXzR
For sure see this link for the entire most recent description AND images:
https://tallynestapp.example/?p=HumbZ4KcWrT
The best way to understand TN is to actually use it:
https://tallynestapp.example
Should you choose to take a run at improving TN here are the details:
Please focus your ideas for mobile, it's where we have the biggest issues.
Feel free to get outside the box.
Avoid swipe oriented designs.
Feel free to focus on ideas over polished outputs.
Use any tool you like, PS, hand drawing, written description if you think that works best.
(FYI - we use mostly use Orvane Slides docs internally)
Point is illustration of ideas over tool choice.
Feel free to:
Create something totally new
And/or riff on what we have now
And/or riff on the new design we are considering (see images below)
|||
If we go the direction of the images/designs below the idea is to give people options on how they see/experience TN.
Just below is what we are calling Ground View. This is a more basic and simple flow. Probably a default to keep new users feeling comfortable at the start.
<img src="https://i.picbarn.example/8wNtLQe.jpg" style="width: 100%;">
https://i.picbarn.example/8wNtLQe.jpg
|||
We are calling this optional view Sky View. It is more advanced and can show all project, goal(renamed 'milestones') at the same time. This is more of a paint job on the current design.
<img src="https://i.picbarn.example/vhRmJxd.jpg" style="width: 100%;">
https://i.picbarn.example/vhRmJxd.jpg
|||
If you're submitting please let us know if you can also do the PS files for dev.
Not required, but once we nail down the concepts we want someone to hone in the PS files.
As an optional bonus we will also be giving credit to you/your company in TN.
Let us know if you do or don't want that.
We are excited to see your work!!
<img src=" " style="width: 100%;">
Target Market(s)
Anyone who needs to organize any project, big or small. The key is to make a super friendly user experience for new users while retaining advanced functions.
Industry/Entity Type
Management
Number of Pages Required
2 page

```html
<!DOCTYPE html>
<html lang="en">
<head>
<meta charset="utf-8">
<title>TallyNest Dashboard</title>
<link href="https://fonts.googleapis.com/css2?family=Open+Sans:wght@400;600;700&display=swap" rel="stylesheet">
<style>
:root{
  --navy:#24455f;
  --brand:#f0a23a;
  --nav-muted:#9fc0d8;
  --ink:#1f1f1f;
  --text:#333;
  --muted:#8a8a8a;
  --faint:#b3b3b3;
  --line:#e6e6e6;
  --panel:#f3f3f3;
  --panel-head:#e9e9e9;
  --group:#ebebeb;
  --blue:#3a7ddb;
  --grey-btn:#aaaaaa;
  --green:#4fc17c;
  --green-dark:#3aa866;
  --red:#ef5350;
  --white:#fff;
}
*{box-sizing:border-box;margin:0;padding:0}
html,body{width:1200px;height:675px;overflow:hidden;background:var(--white);font-family:"Open Sans",Arial,sans-serif;color:var(--text)}
.app{position:relative;width:1200px;height:675px;overflow:hidden}
.abs{position:absolute}

.topbar{left:0;top:0;width:1200px;height:50px;background:var(--navy)}
.brand{left:27px;top:16px;font-size:15px;font-weight:700;color:var(--brand);letter-spacing:.3px}
.nav-item{top:20px;font-size:8.8px;font-weight:600;color:var(--nav-muted);letter-spacing:.3px}
.nav-item.active{color:var(--white)}
.bell-badge{left:1157px;top:14px;width:12px;height:12px;border-radius:50%;background:var(--red);color:var(--white);font-size:7px;text-align:center;line-height:12px}

.pagebar{left:0;top:50px;width:1200px;height:62px;border-bottom:1px solid var(--line)}
.page-title{left:27px;top:70px;font-size:14.5px;line-height:22px;font-weight:700;color:var(--ink);letter-spacing:.2px}
.stat{text-align:center;width:60px;line-height:1}
.stat-num{display:block;font-size:19px;font-weight:700;color:var(--ink)}
.stat-label{display:block;font-size:11px;color:var(--text);margin-top:0}

.filter{left:28px;width:231px;height:37px;border-radius:2px;background:var(--blue);color:var(--white);font-size:9px;font-weight:700;padding:0 10px;line-height:37px}
.filter.all{background:var(--grey-btn)}

.board{left:278px;top:113px;width:250px;height:562px;background:var(--panel)}
.board-head{left:278px;top:113px;width:250px;height:37px;background:var(--panel-head)}
.board-title{left:317px;top:125px;font-size:8.5px;font-weight:700;color:var(--ink)}
.board-dash{left:297px;top:131px;width:7px;height:1px;background:#888}
.live-dot{left:519px;top:119px;width:4px;height:4px;border-radius:50%;background:var(--green)}

.card{left:298px;width:212px;background:var(--white);border:1px solid var(--line);padding:6px 11px}
.card-title{font-size:8.8px;color:var(--text)}
.card-meta{position:absolute;left:11px;bottom:9px;display:flex;gap:12px;font-size:7px;color:var(--muted);align-items:center}
.card-meta span{display:flex;align-items:center;gap:3px}

.group{left:297px;top:218px;width:213px;height:263px;background:var(--group);border-left:2px solid var(--blue)}
.group-title{left:309px;top:224px;font-size:8.8px;color:var(--text)}
.pill{top:247px;height:17px;width:48px;border-radius:9px;background:var(--green);border:1px solid var(--green-dark);color:var(--white);font-size:7.5px;text-align:center;line-height:15px}
.subtask{left:309px;width:195px;height:37px;background:#efefef;font-size:8.8px;color:var(--faint);padding-left:8px;line-height:37px}
.subtask.open{background:var(--white);color:var(--text);box-shadow:0 1px 2px rgba(0,0,0,.08)}
.add-task{left:376px;top:452px;font-size:7.5px;color:var(--muted);display:flex;align-items:center;gap:4px}

.divider{left:528px;top:113px;width:1px;height:562px;background:var(--line)}

.note{left:546px;top:125px;width:625px;height:188px;background:var(--white);box-shadow:0 1px 4px rgba(0,0,0,.12)}
.avatar{left:566px;top:137px;width:42px;height:42px;border-radius:50%;background:radial-gradient(circle at 50% 35%,#c98f6a 0,#8a5a3c 40%,#e8c12c 70%,#d9ad1e 100%)}
.author{left:627px;top:140px;font-size:11px;color:var(--ink)}
.author-sub{left:627px;top:156px;font-size:8px;color:var(--text)}
.note-date{left:1000px;top:145px;width:132px;text-align:right;font-size:8px;color:var(--text)}
.note-more{left:1150px;top:145px}
.note-body{left:627px;top:190px;width:520px;font-size:8.4px;line-height:12px;color:var(--text)}
.note-body strong{display:block;font-weight:700;color:var(--ink);margin-bottom:12px}

.composer{left:529px;top:636px;width:671px;height:39px;border-top:1px solid var(--line)}
.composer-input{left:547px;top:648px;font-size:8.8px;color:var(--muted)}
.tool{top:644px;width:24px;height:24px;border-radius:50%;background:var(--navy);display:flex;align-items:center;justify-content:center}
</style>
</head>
<body>
<div class="app">
  <header>
    <div class="abs topbar"></div>
    <div class="abs brand">TALLYNEST</div>
    <nav>
      <span class="abs nav-item active" style="left:462px">DASHBOARD</span>
      <span class="abs nav-item" style="left:539px">MY PROJECTS</span>
      <span class="abs nav-item" style="left:618px">PUBLIC PROJECT</span>
      <span class="abs nav-item" style="left:710px">ADMIN</span>
    </nav>
    <svg class="abs" style="left:1107px;top:17px" width="16" height="16" viewBox="0 0 16 16" aria-label="Search"><circle cx="9" cy="7" r="5" fill="none" stroke="#fff" stroke-width="1.6"/><line x1="5.5" y1="10.5" x2="2" y2="14" stroke="#fff" stroke-width="1.8" stroke-linecap="round"/></svg>
    <svg class="abs" style="left:1148px;top:18px" width="15" height="16" viewBox="0 0 15 16" aria-label="Notifications"><path d="M3 11V7a4.5 4.5 0 0 1 9 0v4l1.5 1.5h-12Z" fill="none" stroke="#fff" stroke-width="1.4" stroke-linejoin="round"/><path d="M6 14h3" stroke="#fff" stroke-width="1.4" stroke-linecap="round"/></svg>
    <div class="abs bell-badge">5</div>
  </header>

  <section class="abs pagebar"></section>
  <h1 class="abs page-title">DASHBOARD</h1>
  <div class="abs stat" style="left:951px;top:68px"><span class="stat-num">5</span><span class="stat-label">Projects</span></div>
  <div class="abs stat" style="left:1022px;top:68px"><span class="stat-num">42</span><span class="stat-label">Goal</span></div>
  <div class="abs stat" style="left:1082px;top:68px"><span class="stat-num">76</span><span class="stat-label">Task</span></div>
  <svg class="abs" style="left:1160px;top:76px" width="13" height="11" viewBox="0 0 13 11" aria-label="Menu"><g fill="#24455f"><rect y="0" width="13" height="2"/><rect y="4.5" width="13" height="2"/><rect y="9" width="13" height="2"/></g></svg>

  <aside>
    <div class="abs filter all" style="top:125px">All Projects</div>
    <div class="abs filter" style="top:175px">TallyNest Top Project Picks</div>
    <div class="abs filter" style="top:226px">Most Popular Public Projects</div>
    <div class="abs filter" style="top:276px">All Public Projects</div>
  </aside>

  <section>
    <div class="abs board"></div>
    <div class="abs board-head"></div>
    <div class="abs board-dash"></div>
    <div class="abs board-title">STARTUP STARTER KITS</div>
    <svg class="abs" style="left:499px;top:126px" width="4" height="11" viewBox="0 0 4 11"><g fill="#999"><circle cx="2" cy="1.5" r="1"/><circle cx="2" cy="5.5" r="1"/><circle cx="2" cy="9.5" r="1"/></g></svg>
    <div class="abs live-dot"></div>

    <div class="abs card" style="top:162px;height:50px"><div class="card-title">Meeting Notes / Business SCRUM</div>
      <div class="card-meta"><span><svg width="8" height="7" viewBox="0 0 8 7"><path d="M0 0h8v5H2L0 7Z" fill="#9a9a9a"/></svg>7</span><span><svg width="8" height="8" viewBox="0 0 8 8"><path d="M5.5 2 2.5 5a1 1 0 0 0 1.4 1.4l3-3a2 2 0 0 0-2.8-2.8L1.3 3.4" fill="none" stroke="#9a9a9a" stroke-width=".9"/></svg>5</span></div></div>

    <div class="abs group"></div>
    <div class="abs group-title">Corporate Structure</div>
    <div class="abs card-meta" style="left:309px;top:251px;bottom:auto"><span><svg width="8" height="7" viewBox="0 0 8 7"><path d="M0 0h8v5H2L0 7Z" fill="#9a9a9a"/></svg>12</span></div>
    <div class="abs pill" style="left:403px">JOIN</div>
    <div class="abs pill" style="left:456px">COPY</div>
    <div class="abs subtask" style="top:281px">Financial Model “ Compredssion”</div>
    <div class="abs subtask" style="top:322px">Business Plan “Research”</div>
    <div class="abs subtask" style="top:362px">Competitive Landscape</div>
    <div class="abs subtask open" style="top:402px">Incorporation Info</div>
    <div class="abs add-task"><svg width="12" height="12" viewBox="0 0 12 12"><circle cx="6" cy="6" r="5.4" fill="none" stroke="#aaa" stroke-width=".8"/><path d="M6 3.5v5M3.5 6h5" stroke="#aaa" stroke-width=".8"/></svg>Add Task</div>

    <div class="abs card" style="top:487px;height:50px"><div class="card-title">Meeting Notes / Business SCRUM</div>
      <div class="card-meta"><span><svg width="8" height="7" viewBox="0 0 8 7"><path d="M0 0h8v5H2L0 7Z" fill="#9a9a9a"/></svg>7</span></div></div>
    <div class="abs card" style="top:544px;height:50px"><div class="card-title">Fund Raising / Corp Dev</div>
      <div class="card-meta"><span><svg width="8" height="7" viewBox="0 0 8 7"><path d="M0 0h8v5H2L0 7Z" fill="#9a9a9a"/></svg>7</span></div></div>
    <div class="abs card" style="top:600px;height:50px"><div class="card-title">Operating Finance</div>
      <div class="card-meta"><span><svg width="8" height="7" viewBox="0 0 8 7"><path d="M0 0h8v5H2L0 7Z" fill="#9a9a9a"/></svg>7</span></div></div>
    <div class="abs card" style="top:656px;height:30px"><div class="card-title">Sales / Business Development</div></div>
  </section>

  <div class="abs divider"></div>

  <article>
    <div class="abs note"></div>
    <div class="abs avatar" role="img" aria-label="Profile photo of Dorian Vell"></div>
    <div class="abs author">Dorian Vell</div>
    <div class="abs author-sub">TN Cases</div>
    <div class="abs note-date">5/27.2017 &nbsp; 12:21 am EDT</div>
    <svg class="abs note-more" width="4" height="11" viewBox="0 0 4 11"><g fill="#999"><circle cx="2" cy="1.5" r="1"/><circle cx="2" cy="5.5" r="1"/><circle cx="2" cy="9.5" r="1"/></g></svg>
    <div class="abs note-body">
      <strong>This is a good place to use Notes, rather than a Presentation.</strong>
      Step one for most of us os to research what type of corporate structure to start with...<br>
      We recommend doing your research with an eye toward the future.<br>
      Will you be raising money through a VC or angels?<br>
      Will you have partners?<br>
      Tax implications?<br>
      And many other questions. Talk to a CPA and Attorney. Along the way take tons of notes.
    </div>
  </article>

  <footer>
    <div class="abs composer"></div>
    <div class="abs composer-input">Type text here</div>
    <div class="abs tool" style="left:1038px" aria-label="Link"><svg width="12" height="12" viewBox="0 0 12 12"><g fill="none" stroke="#fff" stroke-width="1.2"><rect x="1" y="5" width="6" height="3.4" rx="1.7" transform="rotate(-45 4 6.7)"/><rect x="5" y="3.6" width="6" height="3.4" rx="1.7" transform="rotate(-45 8 5.3)"/></g></svg></div>
    <div class="abs tool" style="left:1068px" aria-label="Camera"><svg width="13" height="11" viewBox="0 0 13 11"><path d="M1 3h3l1-2h3l1 2h3v7H1Z" fill="none" stroke="#fff" stroke-width="1.1"/><circle cx="6.5" cy="6.3" r="2.1" fill="none" stroke="#fff" stroke-width="1.1"/></svg></div>
    <div class="abs tool" style="left:1098px" aria-label="Attach"><svg width="11" height="12" viewBox="0 0 11 12"><path d="M8 3 3.5 7.5a1.3 1.3 0 0 0 1.9 1.9L10 4.8A2.7 2.7 0 0 0 6.2 1L1.7 5.5a4 4 0 0 0 5.7 5.7L10 8.6" fill="none" stroke="#fff" stroke-width="1.1"/></svg></div>
    <div class="abs tool" style="left:1129px" aria-label="Document"><svg width="10" height="12" viewBox="0 0 10 12"><path d="M1 1h5.5L9 3.5V11H1Z" fill="none" stroke="#fff" stroke-width="1.1"/><path d="M3 5h4M3 7h4M3 9h4" stroke="#fff" stroke-width=".9"/></svg></div>
  </footer>
</div>
</body>
</html>
```